Veltrane Group Business Card Design

The CEO is looking for a new trendy look for his business card.
You can stay with current branding or come up with something new/creative. It can be 3D, including Medical Office buildings. You can use our logo in a variety of colors. Please include name, title, company name, company website, email address, cell number

Target Market(s)

Real Estate Development and Construction

Industry/Entity Type

Health care real estate

Contact Information for Business Card

Rohesh Kamdar, CEO M-604.781.2249 E-roheshkamdar@veltrane.com Address:4180 Lindqvist Ave, Harlow Bay, QN 33482 www.veltrane.com

Font styles to use
Other font styles liked:
• Be creative

Requirements
Must have
• Creative, trendy look
Nice to have
• Please go to our website to get a feel- www. veltrane.com
Should not have
• small fonts

```html
<!DOCTYPE html>
<html lang="en">
<head>
<meta charset="UTF-8">
<title>Veltrane Group – Business Card</title>
<link href="https://fonts.googleapis.com/css2?family=Poppins:wght@400;500;600;800&display=swap" rel="stylesheet">
<style>
  :root {
    --brand-red: #b3222f;
    --brand-navy: #1c2d4f;
    --card-white: #f7f7f7;
    --page-bg: #dedede;
  }
  * { margin: 0; padding: 0; box-sizing: border-box; }
  html, body {
    width: 1200px; height: 930px; overflow: hidden;
    background: var(--page-bg);
    font-family: "Poppins", sans-serif;
  }
  .sheet {
    width: 1200px; height: 930px;
    display: flex; flex-direction: column;
    align-items: center; justify-content: center; gap: 50px;
  }
  .card {
    width: 700px; height: 400px;
    box-shadow: 0 4px 14px rgba(0,0,0,0.12);
    position: relative;
  }
  .card--back {
    background: var(--brand-red);
    display: flex; align-items: center; justify-content: center;
  }
  .card--back .wordmark { color: #ffffff; font-size: 78px; }
  .card--front {
    background: var(--card-white);
    display: flex; flex-direction: column; align-items: center;
    padding-top: 58px;
  }
  .wordmark {
    font-weight: 800; letter-spacing: -2px; line-height: 1;
    color: var(--brand-red); white-space: nowrap;
  }
  .card--front .wordmark { font-size: 66px; }
  .holder { text-align: center; margin-top: 28px; }
  .holder__name {
    color: var(--brand-red); font-weight: 600;
    font-size: 24px; letter-spacing: 1px; text-transform: uppercase;
  }
  .holder__title { color: var(--brand-navy); font-size: 17px; margin-top: 2px; }
  .contact {
    display: flex; align-items: stretch; gap: 20px; margin-top: 24px;
    color: var(--brand-navy); font-size: 17px; line-height: 1.45;
  }
  .contact__address { text-align: right; font-style: normal; }
  .contact__divider { width: 2px; background: var(--brand-red); }
  .contact__list { list-style: none; }
  .contact__list li { display: flex; align-items: center; gap: 8px; white-space: nowrap; }
  .contact__list svg { width: 15px; height: 15px; flex: none; }
</style>
</head>
<body>
<main class="sheet">
  <section class="card card--back" aria-label="Card back">
    <span class="wordmark">Veltrane Group</span>
  </section>

  <section class="card card--front" aria-label="Card front">
    <span class="wordmark">Veltrane Group</span>
    <div class="holder">
      <p class="holder__name">Rohesh Kamdar</p>
      <p class="holder__title">CEO</p>
    </div>
    <div class="contact">
      <address class="contact__address">
        4180 Lindqvist Ave<br>Harlow Bay<br>QN 33482
      </address>
      <span class="contact__divider"></span>
      <ul class="contact__list">
        <li>
          <svg viewBox="0 0 24 24" fill="var(--brand-red)"><path d="M6.6 10.8a15.1 15.1 0 0 0 6.6 6.6l2.2-2.2c.3-.3.7-.4 1-.2 1.1.4 2.3.6 3.6.6.6 0 1 .4 1 1V20c0 .6-.4 1-1 1A17 17 0 0 1 3 4c0-.6.4-1 1-1h3.5c.6 0 1 .4 1 1 0 1.3.2 2.5.6 3.6.1.3 0 .7-.2 1z"/></svg>
          604.781.2249
        </li>
        <li>
          <svg viewBox="0 0 24 24" fill="var(--brand-red)"><path d="M2 5h20v14H2z"/><path d="M2 5l10 8 10-8" fill="none" stroke="#fff" stroke-width="1.6"/></svg>
          roheshkamdar@veltrane.com
        </li>
        <li>
          <svg viewBox="0 0 24 24" fill="none" stroke="var(--brand-red)" stroke-width="2"><circle cx="12" cy="12" r="9"/><ellipse cx="12" cy="12" rx="4" ry="9"/><path d="M3 12h18"/></svg>
          www.veltrane.com
        </li>
      </ul>
    </div>
  </section>
</main>
</body>
</html>
```